Parcelwise HQ letterhead and envelope

Design a formal (8.5x11) letterhead and envelope for sales outreach and legal matters. Using design input from https://www.parcelwisehq.example/ and the attached documents.

Industry/Entity Type

Software Service

Requirements
Must have
• These 4 hex colors are our official colors:
• #355c98 [blue]
• #1eb1a2 [teal]
• #fdba12 [gold]
• #f1653b [orange]
• So no other colors besides these should be used.

```html
<!DOCTYPE html>
<html lang="en">
<head>
<meta charset="utf-8">
<title>Parcelwise HQ Letterhead</title>
<link href="https://fonts.googleapis.com/css2?family=Open+Sans:wght@400;600&family=Arimo:wght@700&display=swap" rel="stylesheet">
<style>
  :root {
    --brand-blue: #355c98;
    --brand-teal: #1eb1a2;
    --paper: #ffffff;
    --ink: #1c1c1c;
    --backdrop: #e4e5e6;
  }
  * { box-sizing: border-box; margin: 0; padding: 0; }
  html, body { width: 1200px; height: 945px; overflow: hidden; }
  body { background: var(--backdrop); font-family: "Open Sans", sans-serif; }

  .letterhead {
    position: absolute; left: 252px; top: 22px;
    width: 696px; height: 900px;
    background: var(--paper);
    box-shadow: 0 6px 18px rgba(0,0,0,.12);
    overflow: hidden;
  }
  .letterhead__frame { position: absolute; inset: 0; }

  .brand {
    position: absolute; left: 70px; top: 150px;
    display: flex; align-items: center; gap: 10px;
  }
  .brand__dot { width: 34px; height: 34px; border-radius: 50%; background: var(--brand-blue); }
  .brand__name { font-size: 28px; font-weight: 400; color: var(--brand-blue); letter-spacing: .5px; }

  .contact {
    position: absolute; right: 40px; top: 92px;
    display: flex; gap: 14px; font-size: 8.5px; color: var(--brand-blue); line-height: 13px;
  }
  .contact__list { list-style: none; }
  .contact__list li { display: flex; align-items: center; gap: 5px; }
  .contact__list svg { width: 8px; height: 8px; fill: var(--brand-blue); }
  .contact__office { border-left: 1px solid var(--brand-blue); padding-left: 10px; }
  .contact__office strong { display: block; font-weight: 600; font-size: 9.5px; }

  .letter {
    position: absolute; left: 118px; top: 296px; width: 480px;
    color: var(--ink); font-size: 12.3px; line-height: 16px;
  }
  .letter__greeting { font-family: "Arimo", sans-serif; font-weight: 700; font-size: 15px; margin-bottom: 12px; }
  .letter p { margin-bottom: 16px; }

  .signature {
    display: block; margin: 26px 0 0 10px;
    width: 150px; height: 46px; border-radius: 3px;
    background: linear-gradient(90deg, rgba(28,28,28,.16), rgba(28,28,28,.05));
  }
</style>
</head>
<body>
  <main class="letterhead">
    <svg class="letterhead__frame" viewBox="0 0 696 900" aria-hidden="true">
      <rect width="696" height="900" fill="var(--brand-blue)"/>
      <path d="M0,400 C0,150 90,0 270,0 L696,0 L696,900 L0,900 Z" fill="var(--brand-teal)"/>
      <path d="M0,430 C5,170 110,8 300,0 L696,0 L696,480 C692,745 610,888 400,900 L0,900 Z" fill="var(--paper)"/>
      <path d="M696,505 C698,765 615,893 440,900 L696,900 Z" fill="var(--brand-blue)"/>
      <path d="M696,480 C692,745 610,888 400,900 L440,900 C615,893 698,765 696,505 Z" fill="var(--brand-teal)"/>
    </svg>

    <div class="brand">
      <span class="brand__dot"></span>
      <span class="brand__name">Parcelwise HQ</span>
    </div>

    <div class="contact">
      <ul class="contact__list">
        <li><svg viewBox="0 0 10 10"><path d="M2 0.5 L4 3 L3 4.2 C3.8 5.6 4.6 6.4 5.8 7 L7 6 L9.5 8 L8.3 9.6 C4.5 9.3 0.8 5.5 0.4 1.7 Z"/></svg>(555) 014-2290</li>
        <li><svg viewBox="0 0 10 10"><path d="M0 2 H10 V8 H0 Z M0.8 2.6 L5 5.6 L9.2 2.6" /></svg>jsmith@parcelwisehq.example</li>
        <li><svg viewBox="0 0 10 10"><circle cx="5" cy="5" r="4.5"/></svg>www.parcelwisehq.example</li>
      </ul>
      <div class="contact__office">
        <strong>Parcelwise HQ</strong>
        128 Ledger Row<br>Fairview, MI 40000
      </div>
    </div>

    <article class="letter">
      <h1 class="letter__greeting">Dear Mr. Ellison,</h1>
      <p>Lorem Ipsum is simply dummy text of the printing and typesetting industry. Lorem Ipsum has been the industry's standard dummy text ever since the 1500s, when an unknown printer took a galley of type and scrambled it to make a type specimen book. It has survived not only five centuries, but also the leap into electronic typesetting, remaining essentially unchanged.</p>
      <p>The standard chunk of Lorem Ipsum used since the 1500s is reproduced below for those interested. Sections 1.10.32 and 1.10.33 from "de Finibus Bonorum et Malorum" by Aurelio Vento are also reproduced in their exact original form, accompanied by English versions from the 1914 translation by H. Rowe.</p>
      <p>Lorem Ipsum is simply dummy text of the printing and typesetting industry. Lorem Ipsum has been the industry's standard dummy text ever since the 1500s, when an unknown printer took a galley of type and scrambled it to make a type specimen book. It has survived not only five centuries, but also the leap into electronic typesetting, remaining essentially unchanged. It was popularised in the</p>
      <p>The standard chunk of Lorem Ipsum used since the 1500s is reproduced below for those interested. Sections 1.10.32 and 1.10.33 from "de Finibus Bonorum et Malorum" by Aurelio Vento are also reproduced in their exact original form, accompanied by English versions from the 1914 translation by H. Rowe.</p>
      <p>The standard chunk of Lorem Ipsum used since the 1500s is reproduced below for those interested. Sections 1.10.32 and 1.10.33 from "de Finibus Bonorum et Malorum" by Aurelio Vento are also reproduced in their exact original form.</p>
      <div class="signature" role="img" aria-label="Handwritten signature of the sender"></div>
    </article>
  </main>
</body>
</html>
```